Catering Menu Package

I currently have a complete menu package, which we have redesigned as far as content, now I need to it put together in a catalog type format. It is essentially 10-12 pages in length, and will be sent for print production. Upon receiving a final edit
Updates

I have added an example gif to the project.

I did this free hand this basically what I am looking for. please change text and type to whatever you think would look best. This is a total rough design so, feel free to change any and everything. The text for the page is on the word documents. If you need more images let me know I am in the process of getting as many images uploaded for your use.

Project Deadline Extended
Reason: I figured we got a late jump with questions, so i am extending a few days .

Target Market(s)

The target market is business who wish to have catered luncheons, breakfasts , meetings

Industry/Entity Type

Catering

Requirements
Must have
• I have attached a copy of the text that what we want in the package, our logo, and i have also attached a catering package of another company to give you an idea what the finished product will be
Should not have
• It should not look identical to the example catering packages, these are for some inspiration we want our own design with the same type of look and feel

```html
<!DOCTYPE html>
<html lang="en">
<head>
<meta charset="utf-8">
<title>Catering Menu – Mix &amp; Mingle / Office Party</title>
<link href="https://fonts.googleapis.com/css2?family=Alegreya:ital,wght@0,700;1,400;1,700&family=Libre+Baskerville:wght@400;700&display=swap" rel="stylesheet">
<style>
  :root {
    --canvas: #ebe6de;
    --paper: #ece3d4;
    --paper-edge: #e2d6c3;
    --orange: #ef7a2a;
    --band: #f47a20;
    --green: #6dbb4f;
    --ink: #161616;
    --white: #ffffff;
    --photo-light: #f4efe6;
    --photo-mid: #d9b58f;
    --photo-deep: #b36a3d;
    --bread-light: #eadcc0;
    --bread-mid: #d5b27e;
    --bread-deep: #c27d33;
  }
  * { margin: 0; padding: 0; box-sizing: border-box; }
  html, body { width: 1200px; height: 800px; overflow: hidden; }
  body { background: var(--canvas); position: relative; }

  .menu-page {
    position: absolute; top: 16px; width: 566px; height: 748px;
    background: radial-gradient(ellipse at 40% 40%, var(--paper) 0%, var(--paper-edge) 100%);
    box-shadow: 0 2px 8px rgba(0,0,0,.18);
    overflow: hidden;
  }
  .menu-page--front { left: 22px; }
  .menu-page--back { left: 608px; }

  .food-photo { position: absolute; left: 0; top: 0; }

  .page-title {
    position: absolute; top: 18px; left: 0; width: 430px; text-align: center;
    font-family: "Alegreya", Georgia, serif; font-style: italic; font-weight: 700;
    font-size: 32px; color: var(--orange);
  }
  .menu-page--back .page-title { width: 500px; }

  .item-name {
    position: absolute; left: 20px; width: 360px;
    font-family: "Alegreya", Georgia, serif; font-style: italic; font-weight: 700;
    font-size: 17px; line-height: 21px; color: var(--orange);
  }
  .menu-page--back .item-name { left: 25px; width: 400px; font-size: 16.5px; }
  .item-price {
    position: absolute; left: 336px;
    font-family: "Libre Baskerville", Georgia, serif; font-weight: 700;
    font-size: 16px; line-height: 21px; color: var(--ink);
  }
  .menu-page--back .item-price { left: 343px; }

  .price-note {
    position: absolute; left: 12px; top: 656px; width: 398px; height: 28px;
    background: var(--green); border-radius: 8px; color: var(--white);
    font-family: "Libre Baskerville", Georgia, serif; font-size: 9.5px; line-height: 12px;
    text-align: center; padding-top: 2px;
  }

  .contact-band {
    position: absolute; left: 0; top: 689px; width: 440px; height: 59px;
    background: var(--band); color: var(--white);
  }
  .contact-call {
    position: absolute; left: 20px; top: 4px;
    font-family: "Alegreya", Georgia, serif; font-style: italic; font-size: 10.5px;
  }
  .contact-phone {
    position: absolute; left: 32px; top: 16px; display: flex; align-items: center; gap: 8px;
    font-family: "Alegreya", Georgia, serif; font-style: italic; font-weight: 700;
    font-size: 23px; color: var(--ink);
  }
  .contact-address {
    position: absolute; left: 232px; top: 6px;
    font-family: "Libre Baskerville", Georgia, serif; font-size: 10px; line-height: 14px;
  }

  .brand-box {
    position: absolute; left: 440px; top: 521px; width: 114px; height: 209px;
    background: var(--white);
    display: flex; flex-direction: column; align-items: center; justify-content: center; gap: 10px;
  }
  .brand-mark { width: 28px; height: 28px; border-radius: 50%; background: var(--orange); }
  .brand-name {
    font-family: "Alegreya", Georgia, serif; font-weight: 700;
    font-size: 19px; line-height: 22px; color: var(--ink); text-align: center;
  }
</style>
</head>
<body>

<section class="menu-page menu-page--front">
  <svg class="food-photo" width="566" height="748" role="img" aria-label="Photo of bacon-wrapped scallops with rosemary on a white plate">
    <defs>
      <linearGradient id="scallopTone" x1="0" y1="0" x2="1" y2="1">
        <stop offset="0" stop-color="var(--photo-light)"/>
        <stop offset=".45" stop-color="var(--photo-mid)"/>
        <stop offset=".7" stop-color="var(--photo-deep)"/>
        <stop offset="1" stop-color="var(--photo-light)"/>
      </linearGradient>
    </defs>
    <path d="M440 0 H566 V521 H423 C 442 380 462 200 440 0 Z" fill="url(#scallopTone)"/>
  </svg>

  <h1 class="page-title">The Mix &amp; Mingle</h1>

  <p class="item-name" style="top:67px">Scallops Wrapped in Bacon</p><p class="item-price" style="top:67px">$&amp;.&amp;&amp;</p>
  <p class="item-name" style="top:104px">Shrimp Cocktail</p><p class="item-price" style="top:104px">$&amp;.&amp;&amp;</p>
  <p class="item-name" style="top:139px">Thai Grilled Chicken Bites</p><p class="item-price" style="top:139px">$&amp;.&amp;&amp;</p>
  <p class="item-name" style="top:177px">Served with steamed wild rice</p><p class="item-price" style="top:177px">$&amp;.&amp;&amp;</p>
  <p class="item-name" style="top:219px">Marinated Flank Steak</p><p class="item-price" style="top:219px">$&amp;.&amp;&amp;</p>
  <p class="item-name" style="top:262px">Carved and served with herb mayonnaise &amp;<br>horseradish</p><p class="item-price" style="top:283px">$&amp;.&amp;&amp;</p>
  <p class="item-name" style="top:325px">With fresh rolls &amp; Artisan bread</p><p class="item-price" style="top:325px">$&amp;.&amp;&amp;</p>
  <p class="item-name" style="top:369px">Aged Cheese Board</p><p class="item-price" style="top:369px">$&amp;.&amp;&amp;</p>
  <p class="item-name" style="top:419px;width:400px">Pepper Jack, Smoked Gouda, English Cheddar</p><p class="item-price" style="top:437px">$&amp;.&amp;&amp;</p>
  <p class="item-name" style="top:479px">Goat, Gorgonzola &amp; Aged Swiss</p><p class="item-price" style="top:479px">$&amp;.&amp;&amp;</p>
  <p class="item-name" style="top:522px">Garnished with dried fruit &amp; nuts</p><p class="item-price" style="top:522px">$&amp;.&amp;&amp;</p>
  <p class="item-name" style="top:561px">Served with crackers</p><p class="item-price" style="top:561px">$&amp;.&amp;&amp;</p>
  <p class="item-name" style="top:595px">Mediterranean Pasta Salad</p><p class="item-price" style="top:595px">$&amp;.&amp;&amp;</p>
  <p class="item-name" style="top:629px">Fresh Fruit &amp; Melon Display</p><p class="item-price" style="top:629px">$&amp;.&amp;&amp;</p>

  <p class="price-note">All Prices are per Person, with a 10 person minimum order per item chosen.<br>Local Products used when available and in season</p>

  <footer class="contact-band">
    <p class="contact-call">CALL OR EMAIL US TODAY:</p>
    <p class="contact-phone">
      <svg width="24" height="20" viewBox="0 0 24 20" aria-hidden="true"><path d="M2 7 C2 2 22 2 22 7 L22 9 L17 9 L17 6 L7 6 L7 9 L2 9 Z M6 10 H18 L20 19 H4 Z" fill="var(--ink)"/><circle cx="12" cy="14" r="2.5" fill="var(--band)"/></svg>
      555-014-2290
    </p>
    <p class="contact-address">418 Linden Row<br>Marlow, MD 20999<br>www.harborfieldcaterers.com</p>
  </footer>

  <div class="brand-box">
    <span class="brand-mark"></span>
    <p class="brand-name">Harbor<br>Field<br>Caterers</p>
  </div>
</section>

<section class="menu-page menu-page--back">
  <svg class="food-photo" width="566" height="748" role="img" aria-label="Photo of sliced apricot bread with fresh fruit in the background">
    <defs>
      <linearGradient id="breadTone" x1="0" y1="0" x2="0" y2="1">
        <stop offset="0" stop-color="var(--photo-light)"/>
        <stop offset=".3" stop-color="var(--bread-light)"/>
        <stop offset=".6" stop-color="var(--bread-mid)"/>
        <stop offset=".85" stop-color="var(--bread-deep)"/>
        <stop offset="1" stop-color="var(--bread-light)"/>
      </linearGradient>
    </defs>
    <path d="M440 0 H566 V521 H460 C 470 380 480 200 440 0 Z" fill="url(#breadTone)"/>
  </svg>

  <h1 class="page-title">The Office Party</h1>

  <p class="item-name" style="top:56px">Grilled Marinated London Broil</p><p class="item-price" style="top:56px">$&amp;.&amp;&amp;</p>
  <p class="item-name" style="top:82px">Carved and served with horseradish &amp; port wine<br>mushroom sauce</p><p class="item-price" style="top:103px">$&amp;.&amp;&amp;</p>
  <p class="item-name" style="top:132px">Grilled Whole Mahi Mahi Display</p><p class="item-price" style="top:134px">$&amp;.&amp;&amp;</p>
  <p class="item-name" style="top:168px">Served with fruit salsa</p><p class="item-price" style="top:168px">$&amp;.&amp;&amp;</p>
  <p class="item-name" style="top:206px">Southwest Twice Baked Potato Bites</p><p class="item-price" style="top:206px">$&amp;.&amp;&amp;</p>
  <p class="item-name" style="top:239px;line-height:24px">AStuffed with scallions, bacon, cheese, butter &amp; sour<br>cream</p><p class="item-price" style="top:264px">$&amp;.&amp;&amp;</p>
  <p class="item-name" style="top:291px">Balsamic Fire Roasted Vegetable Medley</p><p class="item-price" style="top:314px">$&amp;.&amp;&amp;</p>
  <p class="item-name" style="top:345px">Fresh Baked Rolls &amp; Artisan Bread</p><p class="item-price" style="top:345px">$&amp;.&amp;&amp;</p>
  <p class="item-name" style="top:377px">Served with whipped butter</p><p class="item-price" style="top:377px">$&amp;.&amp;&amp;</p>
  <p class="item-name" style="top:408px">Bite Sized Italian Sausage</p><p class="item-price" style="top:408px">$&amp;.&amp;&amp;</p>
  <p class="item-name" style="top:437px">With peppers &amp; onions</p><p class="item-price" style="top:437px">$&amp;.&amp;&amp;</p>
  <p class="item-name" style="top:470px">With condiments &amp; fresh baked rolls</p><p class="item-price" style="top:470px">$&amp;.&amp;&amp;</p>
  <p class="item-name" style="top:503px">Buffalo Drummies &amp; Wing Sections</p><p class="item-price" style="top:503px">$&amp;.&amp;&amp;</p>
  <p class="item-name" style="top:540px">Served with bleu cheese dressing, celery &amp;<br>carrot sticks</p><p class="item-price" style="top:559px">$&amp;.&amp;&amp;</p>
  <p class="item-name" style="top:596px">Queso Dip</p><p class="item-price" style="top:596px">$&amp;.&amp;&amp;</p>
  <p class="item-name" style="top:629px">Served with tortilla chips</p><p class="item-price" style="top:629px">$&amp;.&amp;&amp;</p>

  <p class="price-note">All Prices are per Person, with a 10 person minimum order per item chosen.<br>Local Products used when available and in season</p>

  <footer class="contact-band">
    <p class="contact-call">CALL OR EMAIL US TODAY:</p>
    <p class="contact-phone">
      <svg width="24" height="20" viewBox="0 0 24 20" aria-hidden="true"><path d="M2 7 C2 2 22 2 22 7 L22 9 L17 9 L17 6 L7 6 L7 9 L2 9 Z M6 10 H18 L20 19 H4 Z" fill="var(--ink)"/><circle cx="12" cy="14" r="2.5" fill="var(--band)"/></svg>
      555-014-2290
    </p>
    <p class="contact-address">418 Linden Row<br>Marlow, MD 20999<br>www.harborfieldcaterers.com</p>
  </footer>

  <div class="brand-box">
    <span class="brand-mark"></span>
    <p class="brand-name">Harbor<br>Field<br>Caterers</p>
  </div>
</section>

</body>
</html>
```